Stylish Business Cards Wanted

- DOUBLE SIDED Design Required -

High end, edgy cards for a corporate and personal stylist. Must include logo,
Name: Belinda Harwick
Title: Director and Stylist
telephone : +61 8 7142 5809
email: belinda@theloombriefing.example
website: theloombriefing.example
Tag: Corporate Workwear & Uniform Specialist | Personal Stylist
Would like nice icons for telephone, email, website

Target Market(s)

Businesses wanting stylish uniforms, people wanting stylish wardrobes

Industry/Entity Type

Corporate Workwear Stylist

Contact Information for Business Card

I would like black, white and gold foiling incorporated in the design - possibly a touch of the other colours on my branding guide attached Name: Belinda Harwick Title: Director and Stylist telephone : +61 8 7142 5809 email: belinda@theloombriefing.example website: theloombriefing.example Tag: Corporate Workwear & Uniform Specialist | Personal Stylist Would like nice icons for telephone, email, website

Font styles to use
Other font styles liked:
• Raleway

Colors

Designer to choose colors to be used in the design.

Requirements
Must have
• Gold foil accents

```html
<!DOCTYPE html>
<html lang="en">
<head>
<meta charset="utf-8">
<title>The Loom Briefing – Business Cards</title>
<link rel="stylesheet" href="https://fonts.googleapis.com/css2?family=Roboto:wght@400;500;700&display=swap">
<style>
  :root {
    --bg: #1b1b1b;
    --card-black: #222222;
    --card-white: #ffffff;
    --gold: #e5bd52;
    --text-light: #ffffff;
    --text-dark: #222222;
    --card-w: 620px;
    --card-h: 354px;
  }
  * { box-sizing: border-box; margin: 0; padding: 0; }
  html, body {
    width: 1200px; height: 988px; overflow: hidden;
    background: var(--bg);
    font-family: "Roboto", Arial, sans-serif;
  }
  .stage {
    width: 1200px; height: 988px;
    display: flex; flex-direction: column; align-items: center; justify-content: center;
    gap: 60px;
  }
  .card {
    position: relative;
    width: var(--card-w); height: var(--card-h);
    border-radius: 18px;
    overflow: hidden;
  }
  /* Front */
  .card--front { background: var(--card-black); }
  .brand {
    position: absolute;
    display: flex; align-items: center; gap: 12px;
    font-weight: 700; font-size: 40px; letter-spacing: 0.5px;
    white-space: nowrap;
  }
  .brand__mark { width: 14px; height: 14px; background: var(--gold); }
  .card--front .brand { left: 50%; top: 120px; transform: translateX(-50%); color: var(--text-light); }
  .tag-band {
    position: absolute; left: 0; right: 0; top: 262px; height: 34px;
    background: var(--gold);
    display: flex; align-items: center; justify-content: center;
    color: var(--text-light); font-size: 17px; font-weight: 500; letter-spacing: 0.2px;
  }
  /* Back */
  .card--back { background: var(--card-white); }
  .card--back .brand { right: 40px; top: 58px; color: var(--text-dark); font-size: 34px; }
  .wave { position: absolute; inset: 0; width: 100%; height: 100%; }
  .contact {
    position: absolute; left: 56px; top: 198px;
    color: var(--text-light);
  }
  .contact__name { color: var(--gold); font-weight: 700; font-size: 22px; line-height: 26px; letter-spacing: 0.5px; text-transform: uppercase; }
  .contact__title { font-size: 15px; line-height: 20px; margin-top: 1px; }
  .contact__rule { width: 22px; height: 2px; background: var(--gold); margin: 8px 0 6px; }
  .contact__list { list-style: none; }
  .contact__item { display: flex; align-items: center; gap: 10px; font-size: 14px; line-height: 23px; white-space: nowrap; }
  .contact__icon { width: 16px; height: 16px; flex: none; }
  .accent { color: var(--gold); }
</style>
</head>
<body>
<main class="stage">
  <section class="card card--front" aria-label="Business card front">
    <div class="brand"><span class="brand__mark"></span>The Loom Briefing</div>
    <div class="tag-band">Corporate Workwear &amp; Uniform Specialist | Personal Stylist</div>
  </section>

  <section class="card card--back" aria-label="Business card back">
    <svg class="wave" viewBox="0 0 620 354" preserveAspectRatio="none" aria-hidden="true">
      <path d="M0,354 L0,196 C30,178 80,172 180,170 C330,167 450,170 510,156 C575,140 605,108 620,58 L620,354 Z" fill="var(--card-black)"/>
      <path d="M130,162 C240,156 400,158 500,145 C565,134 598,106 612,64" fill="none" stroke="var(--gold)" stroke-width="4" stroke-linecap="round"/>
    </svg>
    <div class="brand"><span class="brand__mark"></span>The Loom Briefing</div>
    <div class="contact">
      <div class="contact__name">Belinda Harwick</div>
      <div class="contact__title">Director and Stylist</div>
      <div class="contact__rule"></div>
      <ul class="contact__list">
        <li class="contact__item">
          <svg class="contact__icon" viewBox="0 0 16 16" aria-hidden="true"><path d="M3.5 1.5l2.5 0.5 1 3-1.6 1.2a8 8 0 0 0 4.4 4.4l1.2-1.6 3 1 .5 2.5-1.8 1.8C7 14 2 9 1.7 3.3z" fill="var(--gold)"/></svg>
          <span>+61 8 7142 5809</span>
        </li>
        <li class="contact__item">
          <svg class="contact__icon" viewBox="0 0 16 16" aria-hidden="true"><rect x="1" y="3.5" width="14" height="9" fill="var(--gold)"/><path d="M1 3.5l7 5 7-5" fill="none" stroke="var(--card-black)" stroke-width="1.3"/></svg>
          <span>belinda@theloombriefing.example</span>
        </li>
        <li class="contact__item">
          <svg class="contact__icon" viewBox="0 0 16 16" aria-hidden="true"><circle cx="8" cy="8" r="7" fill="var(--gold)"/><path d="M1 8h14M8 1c-3 3-3 11 0 14M8 1c3 3 3 11 0 14" fill="none" stroke="var(--card-black)" stroke-width="1"/></svg>
          <span>www.<span class="accent">theloombriefing</span>.example</span>
        </li>
      </ul>
    </div>
  </section>
</main>
</body>
</html>
```